50th Anniversary Gala Save the date Postcard 8.5x5.5 inches

Looking for a 5.5x8.5 in one-sided postcard design for our annual gala. Design needs to include "Save the date" prominently with all the event information included below. Design should be light, include the colors of our logo and elegant. (almost like a wedding save the date). "Threads of Grace" should look like its own logo.

50th Anniversary Gala at The Lodge at Marrow Glen – “Threads of Grace – Celebrating 50 Years of Building Community”
Thursday, October 24
6-11p
The Lodge at Marrow Glen
Sallow Brook Road, Alder Vale, NY
Honoring – TWR Previous Presidents

Target Market(s)

Exisiting donors

Industry/Entity Type

nonprofit

Font styles to use
Serif
Script

Requirements
Must have
• Save the date prominent
Should not have
• should not have a dark background

```html
<!DOCTYPE html>
<html lang="en">
<head>
<meta charset="UTF-8">
<title>Save the Date – 50th Anniversary Gala</title>
<link href="https://fonts.googleapis.com/css2?family=Great+Vibes&family=Montserrat:wght@400;500;600;700;800&display=swap" rel="stylesheet">
<style>
  :root {
    --navy: #1d4587;
    --gold-dark: #9a6a23;
    --gold: #c89634;
    --gold-light: #f2cf5b;
    --paper: #ffffff;
  }
  * { margin: 0; padding: 0; box-sizing: border-box; }
  html, body { width: 847px; height: 1200px; overflow: hidden; background: var(--paper); }
  .card {
    position: relative; width: 847px; height: 1200px; overflow: hidden;
    background: var(--paper);
    font-family: "Montserrat", sans-serif; color: var(--navy); text-align: center;
  }
  .wash { position: absolute; pointer-events: none; }
  .wash--top-left {
    left: -60px; top: -60px; width: 330px; height: 330px;
    background: radial-gradient(circle at 40% 40%, rgba(238,138,114,.75), rgba(244,169,138,.45) 40%, rgba(127,184,198,.25) 62%, rgba(255,255,255,0) 72%);
  }
  .wash--top-right {
    right: -70px; top: -50px; width: 300px; height: 380px;
    background: radial-gradient(ellipse at 60% 40%, rgba(79,118,145,.55), rgba(244,169,138,.5) 40%, rgba(127,184,198,.25) 60%, rgba(255,255,255,0) 72%);
  }
  .wash--bottom-left {
    left: -80px; bottom: -40px; width: 440px; height: 480px;
    background: radial-gradient(ellipse at 30% 60%, rgba(244,169,138,.6), rgba(127,184,198,.55) 38%, rgba(127,184,198,.25) 58%, rgba(255,255,255,0) 72%);
  }
  .wash--bottom-right {
    right: -80px; bottom: -40px; width: 380px; height: 500px;
    background: radial-gradient(ellipse at 55% 50%, rgba(238,138,114,.7), rgba(244,169,138,.5) 36%, rgba(127,184,198,.25) 58%, rgba(255,255,255,0) 72%);
  }
  .wash--center {
    left: 0; top: 430px; width: 847px; height: 330px;
    background: radial-gradient(ellipse at 50% 45%, rgba(247,211,214,.75), rgba(250,225,215,.45) 45%, rgba(255,255,255,0) 72%);
  }
  .brand { position: absolute; top: 78px; left: 0; right: 0; }
  .brand__name {
    display: inline-flex; align-items: center; gap: 10px;
    font-weight: 700; font-size: 26px; color: var(--navy); letter-spacing: .5px;
  }
  .brand__dot { width: 14px; height: 14px; border-radius: 50%; background: var(--gold); }
  .brand__years {
    margin-top: 14px; display: flex; align-items: center; justify-content: center; gap: 10px;
    font-size: 11px; font-weight: 600; letter-spacing: 2px; color: var(--navy);
  }
  .brand__years::before, .brand__years::after { content: ""; width: 70px; height: 1px; background: var(--gold); }
  .headline {
    position: absolute; top: 205px; left: 0; right: 0;
    font-family: "Great Vibes", cursive; font-size: 110px; line-height: 1; font-weight: 400;
    color: var(--gold);
  }
  .event { position: absolute; top: 363px; left: 0; right: 0; font-size: 23px; line-height: 1.4; }
  .event__title { font-weight: 700; }
  .event b { font-weight: 700; }
  .theme { position: absolute; top: 436px; left: 0; right: 0; }
  .theme__title {
    font-weight: 800; font-size: 76px; line-height: 1.3; letter-spacing: -1px;
    background: linear-gradient(90deg, var(--gold-dark), var(--gold-light) 50%, var(--gold-dark));
    -webkit-background-clip: text; background-clip: text; color: transparent;
  }
  .theme__curve { display: block; margin: -14px auto 0; }
  .tagline { position: absolute; top: 670px; left: 0; right: 0; font-size: 29px; font-weight: 500; line-height: 1.25; }
  .date { position: absolute; top: 786px; left: 0; right: 0; display: flex; justify-content: center; align-items: center; }
  .date__side { font-size: 21px; padding: 0 20px; }
  .date__mid { border-left: 1.5px solid var(--gold); border-right: 1.5px solid var(--gold); padding: 0 24px; line-height: 1; }
  .date__month { font-size: 21px; }
  .date__day { font-size: 33px; font-weight: 600; }
  .time { position: absolute; top: 870px; left: 0; right: 0; font-size: 21px; font-weight: 600; }
  .venue { position: absolute; top: 915px; left: 0; right: 0; font-size: 18px; line-height: 1.3; font-style: normal; }
  .rule { position: absolute; top: 1028px; left: 330px; width: 188px; height: 1px; background: linear-gradient(90deg, transparent, var(--gold), transparent); }
  .honor { position: absolute; top: 1047px; left: 0; right: 0; font-size: 17px; line-height: 1.3; }
</style>
</head>
<body>
<main class="card">
  <div class="wash wash--top-left" role="img" aria-label="Watercolour coral and peach flowers with blue-grey leaves"></div>
  <div class="wash wash--top-right" role="img" aria-label="Watercolour peach blossoms with slate-blue foliage"></div>
  <div class="wash wash--center" role="img" aria-label="Soft blush watercolour wash"></div>
  <div class="wash wash--bottom-left" role="img" aria-label="Watercolour flowers and teal leaves"></div>
  <div class="wash wash--bottom-right" role="img" aria-label="Watercolour coral poppies and orange buds"></div>

  <header class="brand">
    <div class="brand__name"><span class="brand__dot"></span>Tidewater Reach</div>
    <div class="brand__years">50 YEARS · 1974 - 2024</div>
  </header>

  <h1 class="headline">Save the Date</h1>

  <section class="event">
    <div class="event__title">50th Anniversary Gala</div>
    <div>at <b>The Lodge</b> at <b>Marrow Glen</b></div>
  </section>

  <section class="theme">
    <div class="theme__title">THREADS OF<br>GRACE</div>
    <svg class="theme__curve" width="370" height="36" viewBox="0 0 370 36" aria-hidden="true">
      <path d="M5 4 Q185 64 365 4 Q185 46 5 4 Z" fill="var(--navy)"/>
    </svg>
  </section>

  <p class="tagline">Celebrating 50 Years of<br>Building Community</p>

  <section class="date">
    <span class="date__side">Thursday</span>
    <span class="date__mid"><span class="date__month">OCT</span><br><span class="date__day">24</span></span>
    <span class="date__side">2024</span>
  </section>

  <p class="time">6.00 – 11.00 p.m.</p>

  <address class="venue">The Lodge at Marrow Glen<br>Sallow Brook Road,<br>Alder Vale, NY</address>

  <div class="rule"></div>

  <p class="honor">Honoring<br>TWR Previous Presidents</p>
</main>
</body>
</html>
```